Business Card

THIS IS THE CARD INFORMATION
DEVELOPMENT I FINANCING I PROPERTY MANAGEMENT
DANIEL OKAFOR
3182 SW 74th Terrace
Cedar Hollow, FL 33491
Telephone I 855.437.2618
Facsimile I 855.437.2675
Industry/Entity Type
Business

```html
<!DOCTYPE html>
<html lang="en">
<head>
<meta charset="utf-8">
<title>Varela Ortiz &amp; Company — Business Card</title>
<link rel="stylesheet" href="https://fonts.googleapis.com/css2?family=Open+Sans:wght@300;400;700&display=swap">
<style>
  :root {
    --plum: #4a0f40;
    --paper: #ffffff;
    --backdrop: #b4b5b7;
    --font: "Open Sans", Arial, sans-serif;
  }
  * { margin: 0; padding: 0; box-sizing: border-box; }
  html, body { width: 1200px; height: 1000px; overflow: hidden; }
  body { background: var(--backdrop); font-family: var(--font); position: relative; }

  .card {
    position: absolute; top: 83px; width: 520px; height: 814px; overflow: hidden;
  }
  .card--front { left: 67px; background: var(--paper); }
  .card--back { left: 609px; background: var(--paper); }
  .card__band { position: absolute; left: 0; width: 100%; background: var(--plum); }
  .card--front .card__band { top: 0; height: 607px; }
  .card--back .card__band { top: 607px; height: 207px; }

  .brand { position: absolute; display: flex; align-items: center; }
  .brand__dot { width: 80px; height: 80px; border-radius: 50%; flex: none; }
  .brand__name { margin-left: 14px; text-align: right; font-weight: 700; line-height: 1; white-space: nowrap; }
  .brand__main { display: block; font-size: 46px; letter-spacing: 0.5px; }
  .brand__sub { display: block; font-size: 20px; margin-top: 5px; }

  .card--front .brand { left: 41px; top: 52px; color: var(--paper); }
  .card--front .brand__dot { background: var(--paper); }
  .card--back .brand { left: 46px; top: 120px; color: var(--plum); }
  .card--back .brand__dot { background: var(--plum); }

  .services { position: absolute; width: 100%; text-align: center; white-space: nowrap; }
  .card--front .services {
    top: 154px; color: var(--paper); font-size: 16px; letter-spacing: 0.3px;
  }
  .services__sep { font-weight: 300; font-size: 19px; margin: 0 1px; }
  .card--back .services {
    top: 208px; color: var(--plum); font-size: 14px; line-height: 25.5px;
  }

  .contact { position: absolute; top: 220px; width: 100%; text-align: center; color: var(--paper); }
  .contact__name { font-weight: 300; font-size: 36px; letter-spacing: 1px; line-height: 1; }
  .contact__address { margin-top: 20px; font-size: 20px; line-height: 31px; }
  .contact__phones { margin-top: 20px; font-size: 20px; line-height: 28px; }
  .contact__email { margin-top: 9px; font-size: 20px; white-space: nowrap; }

  .website {
    position: absolute; top: 338px; width: 100%; text-align: center;
    color: var(--plum); font-size: 26px; white-space: nowrap;
  }

  .emblem { position: absolute; top: 488px; left: 136px; width: 248px; height: 248px; }
</style>
</head>
<body>

<section class="card card--front" aria-label="Business card front">
  <div class="card__band"></div>
  <div class="brand">
    <span class="brand__dot"></span>
    <span class="brand__name">
      <span class="brand__main">VARELA ORTIZ</span>
      <span class="brand__sub">&amp; COMPANY</span>
    </span>
  </div>
  <p class="services">DEVELOPMENT<span class="services__sep">/</span>FINANCING<span class="services__sep">/</span>PROPERTY MANAGEMENT</p>
  <div class="contact">
    <h1 class="contact__name">DANIEL OKAFOR</h1>
    <p class="contact__address">3182 SW 74th Terrace<br>Cedar Hollow, FL 33491</p>
    <p class="contact__phones">Telephone : 855.437.2618<br>Facsimile : 855.437.2675</p>
    <p class="contact__email">Email : dokafor@varelaortizandco.com</p>
  </div>
  <svg class="emblem" viewBox="0 0 248 248" aria-hidden="true">
    <circle cx="124" cy="124" r="120" fill="var(--plum)" stroke="var(--paper)" stroke-width="6"/>
  </svg>
</section>

<section class="card card--back" aria-label="Business card back">
  <div class="card__band"></div>
  <div class="brand">
    <span class="brand__dot"></span>
    <span class="brand__name">
      <span class="brand__main">VARELA ORTIZ</span>
      <span class="brand__sub">&amp; COMPANY</span>
    </span>
  </div>
  <p class="services">DEVELOPMENT<br>FINANCING<br>PROPERTY MANAGEMENT</p>
  <p class="website">www.varelaortizandco.com</p>
  <svg class="emblem" viewBox="0 0 248 248" aria-hidden="true">
    <circle cx="124" cy="124" r="120" fill="var(--paper)" stroke="var(--plum)" stroke-width="6"/>
  </svg>
</section>

</body>
</html>
```